ORV Web Design Project

I'm looking for a small, friendly,functional, information based website. If you go through the attachments, you would know the nature of the business.
Updates

Hi,

I have uploaded a picture of the CEO, Mr. Delvan Kroth PLMAT member. Please feel free to use it whereever appropriate.

Thanks!

Hello, I have uploaded some references. I like the colours used on the bar and would w

Example of a we page . I like this layout for the inside pages.

I am changing the tabs on my website to:

Home
About us
Services
Contact us

The services tab will have three sub pages:

Immigration
Education
AccommodationAccommodation

Target Market(s)

Young international students willing to come to Canada to study, young international students willing to immigrate to Canada, parents of the students

Industry/Entity Type

Business

Requirements
Must have
• ORV HOME
ABOUT US
CONTACT
SERVICES
TAG LINE

The website should look n feel trendy, smart, current, factual, trustworthy etc....
Nice to have
• I am looking for a bold, attractive, eye catchy home page with less text! Something that makes a statement....
Should not have
• No Clip art, flash animation, no bells n whistles please

```html
<!DOCTYPE html>
<html lang="en">
<head>
<meta charset="utf-8">
<title>ORV – Orvane Business Group</title>
<link rel="stylesheet" href="https://fonts.googleapis.com/css2?family=Arimo:wght@400;700&family=PT+Sans:wght@400;700&family=Roboto+Condensed:wght@700&display=swap">
<style>
:root{
  --red:#ed1c24;
  --ink:#222;
  --grey-text:#333;
  --logo-grey:#6d6e70;
  --nav-dark:#222224;
  --btn:#404040;
  --footer:#333333;
  --page:#f9f7f7;
  --border:#d9d4d4;
}
*{box-sizing:border-box;margin:0;padding:0}
html,body{width:1152px;height:1200px;overflow:hidden}
body{position:relative;background:var(--page);font-family:"Arimo",Arial,sans-serif;color:var(--grey-text)}
.abs{position:absolute}

/* header */
.site-header{left:0;top:0;width:1152px;height:144px;background:linear-gradient(#ffffff 0%,#f2f2f2 55%,#dcdcdc 100%)}
.brand{left:128px;top:30px;display:flex;align-items:center;gap:12px;font-family:"PT Sans",sans-serif;font-weight:700;color:var(--logo-grey)}
.brand-mark{width:34px;height:34px;border-radius:50%;background:var(--red);flex:none}
.brand-text .short{display:block;font-size:44px;line-height:44px;letter-spacing:1px}
.brand-text .full{display:block;font-size:22px;line-height:26px}
.follow{left:864px;top:55px;font-family:"Roboto Condensed",sans-serif;font-weight:700;font-size:16px;color:#333}
.social{top:50px;width:31px;height:31px;border-radius:50%}
.social.one{left:964px;background:#0e3c63}
.social.two{left:1006px;background:#1aa1de}

.main-nav{top:107px;left:0;height:30px;font-size:16px;color:#333}
.main-nav span{position:absolute;top:6px;white-space:nowrap}
.nav-active{left:708px;top:107px;width:85px;height:30px;background:var(--nav-dark);color:#fff;font-size:16px;text-align:center;line-height:30px}
.dropdown{left:708px;top:137px;width:143px;height:95px;background:var(--nav-dark);color:#fff;font-size:12.5px;padding:14px 0 0 12px;line-height:26px;z-index:3}

/* hero */
.hero-band{left:0;top:144px;width:1152px;height:310px;background:var(--red)}
.hero-frame{left:97px;top:158px;width:957px;height:282px;background:#fff}
.hero-photo{left:102px;top:163px;width:947px;height:272px;background:linear-gradient(135deg,#7a5a4a 0%,#c99a80 30%,#3c3f6a 55%,#b98a70 75%,#2d2a36 100%)}
.hero-caption{left:712px;top:389px;width:337px;height:44px;background:rgba(255,255,255,.9);font-family:"PT Sans",sans-serif;font-size:29px;line-height:44px;padding-left:10px;color:#222}
.hero-caption em{font-style:normal;color:var(--red)}

/* welcome */
.welcome{left:96px;top:471px;width:948px;height:231px;border:1px solid var(--border);border-radius:4px;background:linear-gradient(#ffffff,#f3eeee)}
.welcome h1{position:absolute;left:14px;top:30px;font-weight:400;font-size:25px;color:#222}
.welcome h1 em,.section-title em{font-style:normal;color:var(--red)}
.welcome p{position:absolute;left:15px;width:890px;font-size:11.5px;line-height:17px;color:#222}
.p1{top:86px}.p2{top:138px}
.btn{position:absolute;background:var(--btn);color:#fff;font-size:12px;border-radius:4px;text-align:center;line-height:28px;height:28px}
.welcome .btn{left:816px;top:170px;width:71px}

/* services */
.section-title{left:98px;top:729px;font-size:21px;font-weight:400;color:#222}
.section-rule{left:219px;top:741px;width:825px;height:2px;background:var(--red)}
.card{top:781px;width:297px;height:242px;border:1px solid var(--border);border-radius:6px;background:linear-gradient(#ffffff,#f3eeee)}
.card h2{position:absolute;top:12px;left:0;width:100%;text-align:center;font-weight:400;font-size:17.5px;color:#222}
.card .thumb{position:absolute;top:38px;width:186px;height:125px;border:3px solid #e2e2e2}
.card p{position:absolute;top:174px;font-size:12px;line-height:17px;color:#222}
.card .btn{top:226px;width:71px}
.c1{left:98px}.c2{left:423px}.c3{left:748px}

/* footer */
.site-footer{left:0;top:1080px;width:1152px;height:120px;background:var(--footer);color:#fff}
.foot-nav{font-size:12px}
.foot-nav span{position:absolute;top:34px;white-space:nowrap}
.copyright{left:104px;top:73px;font-size:12px}
.contact-line{left:810px;font-size:14px;color:#e6e6e6}
.contact-icon{left:772px}
</style>
</head>
<body>

<header class="abs site-header">
  <div class="abs brand">
    <span class="brand-mark"></span>
    <span class="brand-text"><span class="short">ORV</span><span class="full">Orvane Business Group</span></span>
  </div>
  <div class="abs follow">Follow us on:</div>
  <span class="abs social one" role="img" aria-label="Social profile link"></span>
  <span class="abs social two" role="img" aria-label="Social profile link"></span>
</header>

<nav class="abs main-nav">
  <span style="left:542px">Home</span>
  <span style="left:596px">|</span>
  <span style="left:616px">About us</span>
  <span style="left:694px">|</span>
  <span style="left:812px">|</span>
  <span style="left:838px">ORV Mission</span>
  <span style="left:954px">|</span>
  <span style="left:976px">Contacts</span>
</nav>
<div class="abs nav-active">Services</div>
<div class="abs dropdown">Immigration<br>Education<br>Student Accomodation</div>

<section class="abs hero-band"></section>
<div class="abs hero-frame"></div>
<div class="abs hero-photo" role="img" aria-label="Group photo of smiling international students"></div>
<div class="abs hero-caption">Dare to Dream <em>Canadian…</em></div>

<section class="abs welcome">
  <h1>Welcome To <em>Orvane Business Group</em></h1>
  <p class="p1"><b>Delvan Kroth, CEO of Orvane Business Group,</b> has vast knowledge in the field of Student Recruitment &amp; Higher Education. He is an MBA from Canada and is very well known in the India-Canada education corridor since 2004.</p>
  <p class="p2">He has served as India, Africa &amp; Middle East Head for Harrowgate College in the past, in addition to providing consultant services for various elite institutions including, Westmere College, BC, Lindenfield College, Ottawa, Prairieview Technical College, Manitoba, and Saltmarsh College, BC.</p>
  <span class="btn">Read More</span>
</section>

<h2 class="abs section-title">Our <em>Services</em></h2>
<div class="abs section-rule"></div>

<article class="abs card c1">
  <h2>IMMIGRATION</h2>
  <div class="thumb" style="left:52px;background:linear-gradient(135deg,#d8202a 0%,#f4f4f4 45%,#4f86c8 75%,#2a5ea8 100%)" role="img" aria-label="Canadian flag against blue sky"></div>
  <p style="left:22px">Canada has been consistently rated by the United<br>Nations as one of the top countries in the world</p>
  <span class="btn" style="left:112px">Read More</span>
</article>

<article class="abs card c2">
  <h2>EDUCATION</h2>
  <div class="thumb" style="left:56px;background:linear-gradient(135deg,#e7c27a 0%,#e8a23a 35%,#3b86c4 65%,#c8c2bc 100%)" role="img" aria-label="Students walking with books"></div>
  <p style="left:29px">Canada has one of the finest education systems<br>in the world. Every year thousands of students</p>
  <span class="btn" style="left:118px">Read More</span>
</article>

<article class="abs card c3">
  <h2>STUDENT ACCOMODATION</h2>
  <div class="thumb" style="left:59px;background:linear-gradient(135deg,#bfa271 0%,#e8e2d4 45%,#c9b68e 70%,#8ab32c 100%)" role="img" aria-label="Furnished student room with desk and bed"></div>
  <p style="left:29px">We have assisted many international students<br>find a home away from home in Canada.</p>
  <span class="btn" style="left:128px">Read More</span>
</article>

<footer class="abs site-footer">
  <div class="foot-nav">
    <span style="left:104px">Home</span>
    <span style="left:154px">|</span>
    <span style="left:176px">About us</span>
    <span style="left:240px">|</span>
    <span style="left:273px">Services</span>
    <span style="left:342px">|</span>
    <span style="left:371px">ORV Mission</span>
    <span style="left:459px">|</span>
    <span style="left:487px">Contact Us</span>
  </div>
  <div class="abs copyright">Copyright (C) ORV 2013 - 2014 .  All Rights Reserved</div>

  <svg class="abs contact-icon" style="top:34px" width="24" height="18" viewBox="0 0 24 18" aria-hidden="true">
    <rect x="1" y="3" width="22" height="14" rx="1" fill="#d9d9d9"/>
    <path d="M1 4 L12 11 L23 4" fill="none" stroke="#555" stroke-width="1.5"/>
    <path d="M5 3 L12 0 L19 3" fill="#bdbdbd"/>
  </svg>
  <div class="abs contact-line" style="top:35px">Email : info@orvanebusinessgroup.com</div>

  <svg class="abs contact-icon" style="top:70px" width="24" height="18" viewBox="0 0 24 18" aria-hidden="true">
    <path d="M1 6 Q12 -2 23 6 L20 8 L17 5 L7 5 L4 8 Z" fill="#d9d9d9"/>
    <rect x="4" y="8" width="16" height="9" rx="2" fill="#d9d9d9"/>
    <circle cx="12" cy="12.5" r="2.6" fill="#555"/>
  </svg>
  <div class="abs contact-line" style="top:72px">Phone : (705) 555 0142, (705) 555 0187</div>
</footer>

</body>
</html>
```